High end landscpae design and build company needs a more updated brochure / catalogue

to take what we have and enhance it. make it more modern, pleasing to the eye, more creative, more wow factor!

I have images and an example of our current brochure to see what we have done in the past. The color images show what each page of our current brochure looks like. The black and white ones show how the brochure lookes when you were to open it and read it (the current layout)

Let me know if you need the actual individual images to create this.

use the logo color scheme for the brochure

i will try and upload the actual picture files

i actually have until the 30th

high end cliental.

• modern

• refer to current brochure to see the must haves.

```html
<!DOCTYPE html>
<html lang="en">
<head>
<meta charset="utf-8">
<title>Ashgrove – National &amp; Provincial Awards</title>
<link href="https://fonts.googleapis.com/css2?family=Michroma&family=Josefin+Sans:wght@300&family=Cormorant+Garamond:ital,wght@0,500;1,500&display=swap" rel="stylesheet">
<style>
  :root {
    --ink: #050505;
    --ink-warm: #14110b;
    --gold: #b8a060;
    --gold-light: #d9c48c;
    --gold-deep: #8f7a42;
    --white: #ffffff;
  }
  * { margin: 0; padding: 0; box-sizing: border-box; }
  html, body { width: 849px; height: 1200px; overflow: hidden; background: var(--ink); }

  .page {
    position: relative;
    width: 849px;
    height: 1200px;
    overflow: hidden;
    background:
      radial-gradient(ellipse 70% 22% at 50% 17%, rgba(184,160,96,0.16) 0%, transparent 70%),
      linear-gradient(180deg, var(--ink-warm) 0%, var(--ink) 30%, var(--ink) 100%);
  }

  /* fine gold corner accents */
  .corner {
    position: absolute;
    width: 26px;
    height: 26px;
    border-color: var(--gold);
    border-style: solid;
    border-width: 0;
  }
  .corner-tl { left: 14px; top: 14px; border-top-width: 1px; border-left-width: 1px; }
  .corner-tr { right: 14px; top: 14px; border-top-width: 1px; border-right-width: 1px; }
  .corner-bl { left: 14px; bottom: 14px; border-bottom-width: 1px; border-left-width: 1px; }
  .corner-br { right: 14px; bottom: 14px; border-bottom-width: 1px; border-right-width: 1px; }

  /* header */
  .brand {
    position: absolute;
    left: 34px;
    top: 84px;
    display: flex;
    align-items: center;
    gap: 10px;
  }
  .brand-mark {
    width: 10px;
    height: 10px;
    background: var(--gold);
    transform: rotate(45deg);
  }
  .brand-name {
    font-family: "Josefin Sans", sans-serif;
    font-weight: 300;
    font-size: 24px;
    letter-spacing: 5px;
    color: var(--white);
    line-height: 1;
  }
  .headline {
    position: absolute;
    left: 262px;
    top: 68px;
    width: 478px;
    font-family: "Michroma", sans-serif;
    font-weight: 400;
    font-size: 23px;
    letter-spacing: 1.5px;
    line-height: 30px;
    white-space: nowrap;
    background: linear-gradient(90deg, var(--gold-deep) 0%, var(--gold-light) 50%, var(--gold-deep) 100%);
    -webkit-background-clip: text;
    background-clip: text;
    color: transparent;
  }
  .header-rule {
    position: absolute;
    left: 32px;
    top: 123px;
    width: 785px;
    height: 1px;
    background: linear-gradient(90deg, transparent 0%, var(--gold) 12%, var(--gold-light) 50%, var(--gold) 88%, transparent 100%);
  }
  .header-rule::after {
    content: "";
    position: absolute;
    left: 50%;
    top: -4px;
    width: 9px;
    height: 9px;
    margin-left: -4.5px;
    background: var(--ink);
    border: 1px solid var(--gold-light);
    transform: rotate(45deg);
  }

  /* award title */
  .award-title {
    position: absolute;
    left: 0;
    top: 150px;
    width: 849px;
    text-align: center;
    font-family: "Cormorant Garamond", serif;
    font-weight: 500;
    color: var(--white);
  }
  .award-title .org {
    display: inline-flex;
    align-items: center;
    gap: 14px;
    font-size: 17px;
    letter-spacing: 4px;
    line-height: 22px;
    color: var(--gold-light);
  }
  .award-title .org::before,
  .award-title .org::after {
    content: "";
    width: 46px;
    height: 1px;
    background: var(--gold);
  }
  .award-title .name {
    display: block;
    margin-top: 6px;
    font-style: italic;
    font-size: 58px;
    line-height: 62px;
    letter-spacing: 0.5px;
  }

  /* photographs with floating offset frame */
  .photo {
    position: absolute;
    border: 3px solid var(--gold);
    box-shadow: 0 18px 40px rgba(0,0,0,0.6);
  }
  .photo::after {
    content: "";
    position: absolute;
    left: -10px;
    top: -10px;
    right: 8px;
    bottom: 8px;
    border: 1px solid rgba(217,196,140,0.45);
    pointer-events: none;
  }
  .photo-feature {
    left: 40px; top: 292px; width: 777px; height: 476px;
    background:
      radial-gradient(ellipse at 62% 38%, rgba(214,140,80,0.85) 0%, rgba(140,70,45,0.6) 30%, transparent 60%),
      radial-gradient(ellipse at 18% 78%, rgba(120,200,210,0.75) 0%, transparent 40%),
      radial-gradient(ellipse at 52% 86%, rgba(255,170,80,0.7) 0%, transparent 22%),
      linear-gradient(180deg, #5d6f86 0%, #3b3a3a 45%, #4a4a50 75%, #2b2b2e 100%);
  }
  .photo-pool-garden {
    left: 40px; top: 800px; width: 431px; height: 368px;
    background:
      radial-gradient(ellipse at 68% 72%, #33b7e6 0%, #1a98d0 28%, transparent 48%),
      linear-gradient(180deg, #2f4a2a 0%, #3f6430 40%, #8d919a 62%, #b3b7bf 100%);
  }
  .photo-lap-pool {
    left: 509px; top: 800px; width: 308px; height: 368px;
    background:
      radial-gradient(ellipse at 55% 62%, #3f7ea8 0%, #2f6f9a 25%, transparent 45%),
      linear-gradient(180deg, #c9d4e0 0%, #6f8f6a 25%, #d8d6d0 50%, #d9dad6 80%, #4a4f52 100%);
  }
</style>
</head>
<body>
  <main class="page">
    <span class="corner corner-tl"></span>
    <span class="corner corner-tr"></span>
    <span class="corner corner-bl"></span>
    <span class="corner corner-br"></span>

    <div class="brand">
      <span class="brand-mark"></span>
      <span class="brand-name">ASHGROVE</span>
    </div>
    <h1 class="headline">NATIONAL &amp; PROVINCIAL</h1>
    <div class="header-rule"></div>

    <p class="award-title">
      <span class="org">NORTHFIELD LANDSCAPE GUILD</span>
      <span class="name">Awards of Excellence</span>
    </p>

    <div class="photo photo-feature" role="img" aria-label="Evening backyard with lit pool house, waterfall into a pool, Japanese maple, and glass-walled fire table between lounge chairs"></div>
    <div class="photo photo-pool-garden" role="img" aria-label="Freeform pool with stone coping, rock waterfall, lush green trees and teak loungers"></div>
    <div class="photo photo-lap-pool" role="img" aria-label="Modern rectangular lap pool with gravel borders, wooden deck and small cabana"></div>
  </main>
</body>
</html>
```